Business Cards for a law firm

Business cards for our law firm. Use our silhoette logo and OAK PARTNERS - check our website (www.oakpartners.example)

Contact Information for Business Card

our silhouette logo, OAK PARTNERS, 800-555-0147, Dorian Pemberton, dorian@oakpartners.example

Requirements
Must have
• our silhouette logo, OAK PARTNERS, 800-555-0147, Dorian Pemberton, dorian@oakpartners.example

```html
<!DOCTYPE html>
<html lang="en">
<head>
<meta charset="utf-8">
<title>Oak Partners Business Cards</title>
<link rel="stylesheet" href="https://fonts.googleapis.com/css2?family=Montserrat:wght@500;600&family=Open+Sans:wght@400;600;700&display=swap">
<style>
  :root {
    --navy: #24337a;
    --navy-deep: #1c2866;
    --navy-light: #2f3f8f;
    --paper: #ffffff;
    --ink: #333333;
    --muted: #555555;
    --backdrop: #e9eaee;
  }
  * { margin: 0; padding: 0; box-sizing: border-box; }
  html, body { width: 1200px; height: 900px; overflow: hidden; }
  body {
    background: var(--backdrop);
    font-family: "Open Sans", sans-serif;
    position: relative;
  }
  .card {
    position: absolute;
    left: 250px;
    width: 700px;
    height: 400px;
    border-radius: 4px;
    overflow: hidden;
    box-shadow: 0 6px 18px rgba(0,0,0,0.18);
  }
  .card-front { top: 33px; background: var(--paper); }
  .card-back {
    top: 467px;
    background: linear-gradient(160deg, var(--navy-light) 0%, var(--navy) 55%, var(--navy-deep) 100%);
  }
  .wave { position: absolute; inset: 0; width: 700px; height: 400px; }
  .wordmark {
    position: absolute;
    left: 40px;
    top: 44px;
    display: flex;
    align-items: center;
    gap: 12px;
    font-family: "Montserrat", sans-serif;
    font-weight: 600;
    font-size: 24px;
    letter-spacing: 3px;
    color: var(--navy);
  }
  .wordmark-square { width: 22px; height: 22px; background: var(--navy); }
  .contact {
    position: absolute;
    left: 40px;
    top: 104px;
    font-size: 14px;
    line-height: 1.45;
    color: var(--ink);
  }
  .address { margin-bottom: 10px; color: var(--muted); }
  .contact-row { display: flex; align-items: center; gap: 8px; }
  .contact-row svg { width: 12px; height: 12px; fill: var(--navy); flex: none; }
  .person {
    position: absolute;
    right: 62px;
    top: 262px;
    text-align: right;
  }
  .person-name {
    font-weight: 700;
    font-size: 30px;
    color: var(--navy);
    line-height: 1.1;
  }
  .person-role { font-size: 16px; color: var(--ink); }
  .back-wordmark {
    position: absolute;
    left: 200px;
    top: 250px;
    font-family: "Montserrat", sans-serif;
    font-weight: 500;
    font-size: 36px;
    letter-spacing: 5px;
    color: var(--paper);
  }
</style>
</head>
<body>
  <section class="card card-front" aria-label="Business card front">
    <svg class="wave" viewBox="0 0 700 400" aria-hidden="true">
      <path d="M0,210 C170,215 360,320 700,392 L700,400 L0,400 Z" fill="var(--navy)"/>
      <path d="M0,238 C180,245 380,340 620,400" fill="none" stroke="var(--paper)" stroke-width="3"/>
      <rect x="652" y="318" width="48" height="40" fill="var(--navy)"/>
    </svg>

    <div class="wordmark"><span class="wordmark-square"></span>OAK PARTNERS</div>

    <div class="contact">
      <p class="address">418 Maple Grove Ave, #112<br>Fairview, OH 43210</p>
      <p class="contact-row">
        <svg viewBox="0 0 24 24"><path d="M6.6 10.8a15.1 15.1 0 0 0 6.6 6.6l2.2-2.2a1 1 0 0 1 1-.25 11.4 11.4 0 0 0 3.6.57 1 1 0 0 1 1 1V20a1 1 0 0 1-1 1A17 17 0 0 1 3 4a1 1 0 0 1 1-1h3.5a1 1 0 0 1 1 1c0 1.25.2 2.45.57 3.57a1 1 0 0 1-.25 1z"/></svg>
        800-555-0147
      </p>
      <p class="contact-row">
        <svg viewBox="0 0 24 24"><path d="M2 5h20v14H2z M2 5l10 8 10-8" /></svg>
        dorian@oakpartners.example
      </p>
      <p class="contact-row">
        <svg viewBox="0 0 24 24"><circle cx="12" cy="12" r="10"/></svg>
        www.oakpartners.example
      </p>
    </div>

    <div class="person">
      <p class="person-name">Dorian Pemberton</p>
      <p class="person-role">Lawyer</p>
    </div>
  </section>

  <section class="card card-back" aria-label="Business card back">
    <p class="back-wordmark">OAK PARTNERS</p>
  </section>
</body>
</html>
```